Business Card Design Project

We are a construction company in Orange County, CA. We need a two sided business card. We would like the back to be our logo with web URL. Front should included Name, title, address, phone, fax and email address.

our address is
627 West Dorrance Blvd, Suite 308
Anaheim, CA 92718

Our logo files are attached.

Construction

```html
<!DOCTYPE html>
<html lang="en">
<head>
<meta charset="utf-8">
<title>Bravon Business Card</title>
<link rel="stylesheet" href="https://fonts.googleapis.com/css2?family=Source+Sans+3:ital,wght@0,400;0,600;0,700;1,700&display=swap">
<style>
  :root {
    --backdrop: #d9d9d9;
    --card-white: #ffffff;
    --brand-blue: #114a7f;
    --ink: #3a3a3a;
    --ink-strong: #2e2e2e;
    --back-start: #13477a;
    --back-mid: #252a3a;
    --back-end: #050505;
    --reverse: #ffffff;
  }
  * { box-sizing: border-box; margin: 0; padding: 0; }
  html, body {
    width: 960px;
    height: 1200px;
    overflow: hidden;
    background: var(--backdrop);
    font-family: "Source Sans 3", "Myriad Pro", Arial, sans-serif;
  }
  .canvas {
    position: relative;
    width: 960px;
    height: 1200px;
  }
  .card {
    position: absolute;
    left: 55px;
    width: 840px;
    border-radius: 30px;
    box-shadow: 0 4px 10px rgba(0, 0, 0, 0.25);
    text-align: center;
  }
  .card--front {
    top: 85px;
    height: 478px;
    background: var(--card-white);
    color: var(--ink);
  }
  .card--back {
    top: 645px;
    height: 477px;
    background: linear-gradient(90deg, var(--back-start) 0%, var(--back-mid) 50%, var(--back-end) 100%);
    color: var(--reverse);
  }
  .company-name {
    position: absolute;
    left: 0;
    right: 0;
    font-weight: 700;
    letter-spacing: 2px;
    line-height: 1;
  }
  .card--front .company-name {
    top: 80px;
    font-size: 136px;
    color: var(--brand-blue);
  }
  .card--back .company-name {
    top: 140px;
    font-size: 156px;
    color: var(--reverse);
  }
  .contact {
    position: absolute;
    left: 0;
    right: 0;
    top: 306px;
    font-size: 21px;
    line-height: 38px;
  }
  .contact__name {
    font-size: 26px;
    font-weight: 600;
    color: var(--ink-strong);
    margin-bottom: 6px;
  }
  .contact__title {
    font-size: 21px;
    font-weight: 600;
  }
  .contact__label {
    font-weight: 700;
    font-style: italic;
  }
  .contact__divider {
    margin: 0 8px;
  }
  .web-address {
    position: absolute;
    left: 0;
    right: 0;
    top: 398px;
    font-size: 30px;
    font-weight: 700;
  }
</style>
</head>
<body>
<main class="canvas">
  <section class="card card--front" aria-label="Business card front">
    <div class="company-name">BRAVON</div>
    <div class="contact">
      <p class="contact__name">Your Name, <span class="contact__title">Designation</span></p>
      <p><span class="contact__label">e</span> : info@bravonbuild.com<span class="contact__divider">|</span><span class="contact__label">w</span> : www.bravonbuild.com</p>
      <p><span class="contact__label">p</span> : 1-555-0148<span class="contact__divider">|</span><span class="contact__label">f</span> : 1-555-0149</p>
      <p>627 West Dorrance Blvd, Suite 308, Anaheim, CA 92718</p>
    </div>
  </section>

  <section class="card card--back" aria-label="Business card back">
    <div class="company-name">BRAVON</div>
    <p class="web-address">www.bravonbuild.com</p>
  </section>
</main>
</body>
</html>
```